Falkrin homes and renovations business card design.

Would like some new card designs utilizing my new logo that look professional. I am open to different colors on the logo or utilize the same ones we have. I like the original concept but would like to see some fresh ideas and build on what we have already done.

Target Market(s)

Custom home building industry, Real estate sales, Renovation projects.

Industry/Entity Type

Home Builder

Contact Information for Business Card

Falkrin Homes and Renovations
2871 96th Avenue
Ashvale, Northmere
T2R3W8
Home : 403- 718-4063 Cell: 403- 294-5170

My info is : Dax Falkrin, President and CEO
email: falkrinhomes@maildrop-example.net
Website: falkrinhomes-example.com
websit

Requirements
Must have
• Must Use my new logo design. I am open to different colors on the logo or utilize the same ones in the existing design. I can upload the original logo design if needed.

```html
<!DOCTYPE html>
<html lang="en">
<head>
<meta charset="utf-8">
<title>Falkrin Homes and Renovations – Business Card</title>
<link href="https://fonts.googleapis.com/css2?family=Exo+2:wght@700&family=Open+Sans:wght@400;600&display=swap" rel="stylesheet">
<style>
  :root {
    --page: #d9d9d9;
    --card: #1c1c1c;
    --card-edge: #141414;
    --gold: #c8912a;
    --yellow: #f4b41a;
    --text: #f1f1f1;
  }
  * { box-sizing: border-box; margin: 0; padding: 0; }
  html, body {
    width: 1200px; height: 1000px; overflow: hidden;
    background: var(--page);
    font-family: "Open Sans", Arial, sans-serif;
  }
  .canvas { position: relative; width: 1200px; height: 1000px; }
  .card {
    position: absolute; left: 220px; width: 760px; height: 434px;
    background: var(--card);
    border: 1px solid var(--card-edge);
    box-shadow: 0 6px 18px rgba(0,0,0,0.25);
    color: var(--text);
  }
  .card--back { top: 40px; }
  .card--front { top: 526px; }

  .brand-name {
    font-weight: 600; color: var(--gold);
    text-transform: uppercase; line-height: 1.1; white-space: nowrap;
    display: inline-flex; align-items: center; gap: 12px;
  }
  .brand-name .mark { width: 14px; height: 14px; background: var(--gold); display: inline-block; flex: none; }

  /* Back */
  .back-brand { position: absolute; left: 0; right: 0; top: 170px; text-align: center; }
  .back-brand .brand-name { font-size: 32px; letter-spacing: 1px; }
  .back-web {
    position: absolute; left: 0; right: 0; bottom: 56px;
    font-size: 17px; letter-spacing: 1.5px; color: var(--text);
    display: flex; justify-content: center; align-items: center; gap: 10px;
  }
  .back-web .accent { color: var(--yellow); }

  /* Front */
  .front-brand { position: absolute; left: 44px; top: 40px; font-size: 25px; letter-spacing: 0.5px; }
  .person { position: absolute; left: 44px; top: 124px; }
  .person-name {
    font-family: "Exo 2", Arial, sans-serif; font-weight: 700;
    font-size: 27px; line-height: 32px; color: var(--yellow); letter-spacing: 1.5px; text-transform: uppercase;
  }
  .person-title { font-size: 15px; line-height: 20px; color: var(--text); }
  .address { position: absolute; left: 44px; top: 210px; font-size: 15px; line-height: 22px; font-style: normal; letter-spacing: 0.5px; }
  .contacts { position: absolute; left: 44px; top: 286px; list-style: none; font-size: 15px; letter-spacing: 0.5px; }
  .contacts li { display: flex; align-items: center; height: 23px; }
  .contacts .icon { width: 24px; display: inline-flex; }
  .front-logo { position: absolute; right: 40px; bottom: 44px; font-size: 22px; }
</style>
</head>
<body>
<main class="canvas">

  <section class="card card--back" aria-label="Business card back">
    <div class="back-brand">
      <span class="brand-name"><span class="mark"></span>Falkrin Homes and Renovations</span>
    </div>
    <p class="back-web">
      <svg width="16" height="16" viewBox="0 0 16 16" aria-hidden="true"><circle cx="9" cy="7" r="5" fill="none" stroke="var(--yellow)" stroke-width="2"/><line x1="5.5" y1="10.5" x2="2" y2="14" stroke="var(--yellow)" stroke-width="2"/></svg>
      <span>www.<span class="accent">falkrinhomes-example</span>.com</span>
    </p>
  </section>

  <section class="card card--front" aria-label="Business card front">
    <div class="brand-name front-brand">Falkrin Homes and Renovations</div>

    <div class="person">
      <h1 class="person-name">Dax Falkrin</h1>
      <p class="person-title">President and CEO</p>
    </div>

    <address class="address">2871 96th Avenue<br>Ashvale, Northmere</address>

    <ul class="contacts">
      <li><span class="icon"><svg width="13" height="13" viewBox="0 0 16 16" aria-hidden="true"><path d="M3 1l3 3-2 2c1 2.5 3.5 5 6 6l2-2 3 3-2 2C7 15 1 9 1 3z" fill="var(--gold)"/></svg></span>403 718 4063</li>
      <li><span class="icon"><svg width="11" height="15" viewBox="0 0 11 16" aria-hidden="true"><rect x="1" y="1" width="9" height="14" rx="1.5" fill="none" stroke="var(--gold)" stroke-width="1.5"/><line x1="4" y1="12.5" x2="7" y2="12.5" stroke="var(--gold)" stroke-width="1.5"/></svg></span>403 294 5170</li>
      <li><span class="icon"><svg width="15" height="11" viewBox="0 0 16 12" aria-hidden="true"><rect x="0" y="0" width="16" height="12" fill="var(--gold)"/><path d="M0 0l8 6 8-6" fill="none" stroke="var(--card)" stroke-width="1.5"/></svg></span>falkrinhomes@maildrop-example.net</li>
      <li><span class="icon"><svg width="14" height="14" viewBox="0 0 16 16" aria-hidden="true"><circle cx="9" cy="7" r="5" fill="none" stroke="var(--gold)" stroke-width="2"/><line x1="5.5" y1="10.5" x2="2" y2="14" stroke="var(--gold)" stroke-width="2"/></svg></span>www.falkrinhomes-example.com</li>
    </ul>

    <div class="brand-name front-logo"><span class="mark"></span>Falkrin</div>
  </section>

</main>
</body>
</html>
```